MarbleTrove - New Website Design

Create a professional Vendora website for the hottest trend; a box of school supplies subscription box business called MarbleTrove. Vendora.com is an easy to use website builder.
Please see fizwickpod.com; plumfolly.com; tarrowmintloft.com; and nipcove.com for the concept I am after. The business has not been launched yet, I am currently in the pre-launch stage using a specialized landing page website, and so the time scale for developing my professional looking Vendora website is up to 1-2 weeks.
The webpage should have a fun feel and should match the style of the company logo at plumfolly.com. The pages to include are 'Home', 'About us' and 'Get Started'
Thank you and good luck!
1 page

```html
<!DOCTYPE html>
<html lang="en">
<head>
<meta charset="utf-8">
<title>MarbleTrove – School Supply Box</title>
<link rel="stylesheet" href="https://fonts.googleapis.com/css2?family=Roboto+Slab:wght@300;400;700&family=Roboto:wght@400;500;700&display=swap">
<style>
:root{
  --orange:#f25a0c;
  --orange-light:#ff7a22;
  --ink:#222222;
  --text:#444444;
  --muted:#777777;
  --line:#dddddd;
  --paper:#ffffff;
  --grey-band:#eeecea;
  --soft-band:#f6f3f1;
  --footer:#0b0b0b;
  --footer-text:#d8d8d8;
}
*{box-sizing:border-box;margin:0;padding:0}
html,body{width:1200px;height:3750px;overflow:hidden}
body{position:relative;background:var(--paper);font-family:"Roboto",Arial,sans-serif;color:var(--text)}
.abs{position:absolute}
.slab{font-family:"Roboto Slab",Georgia,serif}
.section-title{position:absolute;left:0;width:1200px;text-align:center;font-family:"Roboto Slab",Georgia,serif;font-weight:300;font-size:32px;color:var(--ink)}
.section-title b{font-weight:700}
.section-title::after{content:"";display:block;width:60px;height:2px;background:var(--ink);margin:14px auto 0}
.btn{position:absolute;display:flex;align-items:center;justify-content:center;font-family:"Roboto Slab",Georgia,serif;font-weight:700;font-size:17px;color:#fff;background:linear-gradient(var(--orange-light),var(--orange));border-radius:3px}

/* hero */
.hero{position:absolute;left:0;top:0;width:1200px;height:625px;background:linear-gradient(100deg,#5e6a55 0%,#b99a86 30%,#d9c6b8 55%,#a8564a 78%,#6b4b3d 100%)}
.hero-shade{position:absolute;inset:0;background:linear-gradient(rgba(0,0,0,.25),rgba(0,0,0,0) 30%,rgba(0,0,0,.1))}
.brand{position:absolute;left:110px;top:18px;display:flex;align-items:center;gap:12px;font-family:"Roboto Slab",Georgia,serif;font-weight:700;font-size:31px;color:#fff}
.brand-mark{width:26px;height:26px;background:#fff;border-radius:50%}
.nav-tools{position:absolute;right:110px;top:20px;display:flex;align-items:center;gap:30px;color:#fff;font-weight:700;font-size:16px}
.hero-title{position:absolute;left:0;top:262px;width:1200px;text-align:center;color:#fff;font-family:"Roboto Slab",Georgia,serif;font-weight:700;font-size:56px;text-shadow:0 2px 6px rgba(0,0,0,.35)}
.hero-sub{position:absolute;left:0;top:330px;width:1200px;text-align:center;color:#fff;font-family:"Roboto Slab",Georgia,serif;font-weight:700;font-size:32px;text-shadow:0 2px 6px rgba(0,0,0,.35)}
.btn-ghost{background:#f2f2f2;color:var(--ink);font-weight:400}
.dots{position:absolute;left:560px;top:572px;display:flex;gap:10px}
.dots span{width:12px;height:12px;border-radius:50%;border:2px solid #fff}
.dots span.on{background:#fff}

/* welcome */
.lead{position:absolute;left:175px;top:738px;width:850px;text-align:center;font-size:15px;line-height:26px;color:var(--text)}
.welcome-box{position:absolute;left:388px;top:812px;width:437px;height:400px;background:linear-gradient(#d94a3a 0%,#f0c23a 25%,#4aa7d8 45%,#d8a86a 60%,#c98f54 100%);border-radius:4px}

/* how it works */
.how{position:absolute;left:0;top:1275px;width:1200px;height:425px;background:linear-gradient(90deg,#f3ebe8,#f8f6f5 40%,#f4eceb 100%)}
.step{position:absolute;width:300px;text-align:center}
.step h3{font-family:"Roboto Slab",Georgia,serif;font-weight:700;font-size:20px;color:var(--ink);margin:22px 0 12px}
.step p{font-size:14px;line-height:21px;color:var(--text)}

/* testimonials */
.avatar{position:absolute;width:86px;height:86px;border-radius:50%;background:linear-gradient(#b6a89a,#7d6a5c)}
.quote{position:absolute;width:285px;font-size:15px;line-height:25.5px;text-align:justify;color:var(--text)}
.quote cite{display:block;margin-top:14px;font-style:normal;font-weight:700;font-size:13px;color:var(--ink)}

/* order */
.order{position:absolute;left:0;top:2125px;width:1200px;height:595px;background:var(--grey-band)}
.product-frame{position:absolute;left:190px;top:2262px;width:385px;height:256px;background:#fff;border:1px solid #e0dcd8;padding:14px}
.product-photo{width:100%;height:100%;background:linear-gradient(135deg,#cfd9de,#b98b59 55%,#d9a86a)}
.thumbs{position:absolute;left:275px;top:2537px;display:flex;gap:20px}
.thumbs span{width:40px;height:33px;border:1px solid #cfc9c3;background:linear-gradient(135deg,#e3ddd5,#b69070)}
.product-name{position:absolute;left:618px;top:2258px;font-family:"Roboto Slab",Georgia,serif;font-weight:700;font-size:21px;color:var(--ink)}
.price{position:absolute;left:618px;top:2290px;font-family:"Roboto Slab",Georgia,serif;font-weight:700;font-size:30px;color:var(--orange)}
.select{position:absolute;left:618px;width:365px;height:38px;background:#e2dedb;display:flex;align-items:center;justify-content:space-between;padding:0 16px;font-size:13px;color:#888}
.qty-label{position:absolute;left:628px;top:2466px;font-size:14px;color:var(--ink)}
.qty{position:absolute;left:700px;top:2458px;width:42px;height:40px;background:#e2dedb;display:flex;align-items:center;justify-content:center;font-size:13px;color:#555}
.desc{position:absolute;left:625px;top:2522px;width:360px;font-size:14px;line-height:23px;color:var(--text)}
.info{position:absolute;left:625px;display:flex;align-items:center;gap:10px;font-size:14px;color:var(--text)}
.info i{width:13px;height:13px;border-radius:50%;background:var(--orange);display:block}

/* gallery */
.gallery{position:absolute;left:190px;top:2855px;display:flex;gap:25px}
.gallery span{width:117px;height:115px;border:3px solid #fff;box-shadow:0 0 0 1px #ddd}

/* newsletter */
.newsletter{position:absolute;left:0;top:3100px;width:1200px;height:287px;background:linear-gradient(90deg,#f3e4e1,#f7f2f0 45%,#f2e1df)}
.field{position:absolute;left:350px;top:3260px;width:375px;height:42px;background:#e9e6e4;display:flex;align-items:center;padding-left:16px;font-size:13px;color:#999}

/* footer */
.footer{position:absolute;left:0;top:3387px;width:1200px;height:363px;background:var(--footer);color:var(--footer-text)}
.col{position:absolute;top:53px;font-size:13px}
.col h4{font-family:"Roboto Slab",Georgia,serif;font-weight:700;font-size:15px;color:#fff;letter-spacing:.5px;margin-bottom:24px}
.col li{list-style:none;line-height:26px}
.social li{display:flex;align-items:center;gap:12px}
.social li::before{content:"";width:8px;height:8px;border-radius:50%;background:#ccc}
.share{display:flex;gap:8px;margin-top:18px}
.share span{padding:6px 9px;background:#3a3a3a;border:1px solid #555;border-radius:2px;font-size:11px;color:#ddd}
.copy{position:absolute;left:152px;top:268px;font-size:12px;color:#ccc}
.pay{position:absolute;left:152px;top:305px;display:flex;gap:18px;align-items:center;font-family:"Roboto",Arial,sans-serif;font-weight:700;font-size:15px;color:#8a8a8a}
</style>
</head>
<body>

<!-- hero -->
<header class="hero" role="img" aria-label="Classroom photo of smiling children with a teacher and a box full of school supplies">
  <div class="hero-shade"></div>
</header>
<div class="brand"><span class="brand-mark"></span>MarbleTrove</div>
<nav class="nav-tools">
  <span>ENG &#8964;</span>
  <svg width="24" height="24" viewBox="0 0 24 24" fill="none" stroke="#fff" stroke-width="3"><circle cx="10" cy="10" r="7"/><path d="M15 15l7 7"/></svg>
  <svg width="24" height="24" viewBox="0 0 24 24" fill="#fff"><path d="M4 8h16l-1 14H5z"/><path d="M8 8V5a4 4 0 0 1 8 0v3" fill="none" stroke="#fff" stroke-width="2"/></svg>
  <svg width="26" height="22" viewBox="0 0 26 22" fill="#fff"><rect y="1" width="26" height="3"/><rect y="9" width="26" height="3"/><rect y="17" width="26" height="3"/></svg>
</nav>
<h1 class="hero-title">The Hottest trend</h1>
<p class="hero-sub">a box of school supplies.</p>
<a class="btn" style="left:440px;top:405px;width:175px;height:45px">Subscribe Now</a>
<a class="btn btn-ghost" style="left:630px;top:405px;width:132px;height:45px">Give a Gift</a>
<div class="dots"><span class="on"></span><span></span><span></span></div>

<!-- welcome -->
<h2 class="section-title" style="top:662px">Welcome To <b>MarbleTrove</b></h2>
<p class="lead">Duis aute irure dolor in reprehenderit in voluptate velit esse cillum dolore eu fugiat nulla pariatur. Excepteur sint occaecat cupidatat non proident,</p>
<div class="welcome-box" role="img" aria-label="Cardboard box overflowing with markers, pens, rulers and school supplies"></div>

<!-- how it works -->
<section class="how" role="img" aria-label="Faded background of colourful stationery"></section>
<h2 class="section-title" style="top:1300px">How It <b>Works</b></h2>
<div class="step" style="left:138px;top:1395px">
  <svg width="70" height="92" viewBox="0 0 70 92" fill="none" stroke="#f25a0c" stroke-width="4" stroke-linejoin="round"><path d="M22 52V10a7 7 0 0 1 14 0v30l20 5a8 8 0 0 1 6 9l-5 28H26L10 60a6 6 0 0 1 9-8z"/><path d="M26 88h32"/></svg>
  <h3>Step One</h3>
  <p>Lorem ipsum dolor sit amet,<br>consectetur adipiscing elit incididunt</p>
</div>
<div class="step" style="left:450px;top:1395px">
  <svg width="84" height="92" viewBox="0 0 84 92" fill="none" stroke="#f25a0c" stroke-width="4" stroke-linejoin="round"><path d="M6 20L18 6h48l12 14v62H6z"/><path d="M6 20h72M26 40h32M26 52h32M26 64h20"/></svg>
  <h3>Step Two</h3>
  <p>Lorem ipsum dolor sit amet,<br>consectetur adipiscing elit incididunt</p>
</div>
<div class="step" style="left:762px;top:1395px">
  <svg width="100" height="92" viewBox="0 0 100 92" fill="none" stroke="#f25a0c" stroke-width="4" stroke-linejoin="round"><path d="M46 8l28 10v26L46 54 18 44V18z"/><path d="M18 18l28 10 28-10M46 28v26"/><path d="M4 64l18-6 24 8h14a5 5 0 0 1 0 10H40"/><path d="M60 72l24-12a6 6 0 0 1 6 10L62 86H28L4 80"/></svg>
  <h3>Step Three</h3>
  <p>Lorem ipsum dolor sit amet,<br>consectetur adipiscing elit incididunt</p>
</div>

<!-- testimonials -->
<h2 class="section-title" style="top:1752px">Testimonials</h2>
<div class="avatar" style="left:175px;top:1847px" role="img" aria-label="Portrait photo of William"></div>
<blockquote class="quote" style="left:280px;top:1847px">“Duis aute irure dolor in reprehenderit in voluptate velit esse cillum dolore eu fugiat nulla pariatur. Excepteur sint occaecat cupidatat non proident, sunt in culpa qui officia deserunt mollit anim id est laborum.”<cite>- William</cite></blockquote>
<div class="avatar" style="left:640px;top:1847px" role="img" aria-label="Portrait photo of Jancy"></div>
<blockquote class="quote" style="left:743px;top:1847px">“Duis aute irure dolor in reprehenderit in voluptate velit esse cillum dolore eu fugiat nulla pariatur. Excepteur sint occaecat cupidatat non proident, sunt in culpa qui officia deserunt mollit anim id est laborum.”<cite>- Jancy</cite></blockquote>

<!-- order -->
<section class="order"></section>
<h2 class="section-title" style="top:2150px">Order <b>Now</b></h2>
<div class="product-frame"><div class="product-photo" role="img" aria-label="Open cardboard box filled with books, folders and office supplies"></div></div>
<div class="thumbs"><span></span><span></span><span></span><span></span></div>
<h3 class="product-name">Finibus Bonorum et Malorum</h3>
<p class="price">$29.00</p>
<div class="select" style="top:2340px">No Of Supplies <span>&#8964;</span></div>
<div class="select" style="top:2400px">Items Need <span>&#8964;</span></div>
<span class="qty-label">Quantity</span>
<div class="qty">1</div>
<a class="btn" style="left:760px;top:2457px;width:105px;height:41px;font-family:Roboto,Arial,sans-serif;font-size:14px">Buy Now</a>
<p class="desc">Nemo enim ipsam voluptatem quia voluptas sit aspernatur aut odit aut fugit, sed quia consequuntur magni dolores eos qui ratione voluptatem sequi nesciunt.</p>
<div class="info" style="top:2614px"><i></i>Get Some Info</div>
<div class="info" style="top:2646px"><i></i>Ask a Question</div>

<!-- gallery -->
<h2 class="section-title" style="top:2760px">Find Us On <b>Snapgrid</b></h2>
<div class="gallery" role="img" aria-label="Six photos of children with school supplies">
  <span style="background:linear-gradient(#3f8fc4,#c7a07a)"></span>
  <span style="background:linear-gradient(#e6ddd2,#b78b62)"></span>
  <span style="background:linear-gradient(#f0d47a,#4f8fd0)"></span>
  <span style="background:linear-gradient(#8b7460,#d2b48d)"></span>
  <span style="background:linear-gradient(#d8c9b6,#e28b5b)"></span>
  <span style="background:linear-gradient(#e8e2dc,#b7463c)"></span>
</div>
<a class="btn" style="left:540px;top:3000px;width:120px;height:40px;font-family:Roboto,Arial,sans-serif;font-size:14px">Follow Us</a>

<!-- newsletter -->
<section class="newsletter" role="img" aria-label="Faded background of school supplies with chalk lettering"></section>
<h2 class="section-title" style="top:3138px">Keep in <b>Touch!</b></h2>
<p class="abs" style="left:0;top:3202px;width:1200px;text-align:center;font-size:12px;color:var(--muted)">Use this section to let customers sign up for your store newsletter.</p>
<div class="field">your@email.com</div>
<a class="btn" style="left:730px;top:3260px;width:120px;height:42px;font-family:Roboto,Arial,sans-serif;font-size:14px">Subscribe</a>

<!-- footer -->
<footer class="footer">
  <div class="col" style="left:155px"><h4>NAVIGATE</h4><ul><li>Home</li><li>Catalog</li><li>Blog</li><li>About Us</li><li>Contact Us</li><li>Features</li></ul></div>
  <div class="col" style="left:335px"><h4>STORE HELP</h4><ul><li>FAQ</li><li>Returns</li><li>Shipping</li><li>Privacy Policy</li></ul></div>
  <div class="col social" style="left:525px"><h4>FIND US ONLINE</h4><ul><li>Friendwall</li><li>Chirper</li><li>Pinmosaic</li><li>Snapgrid</li></ul></div>
  <div class="col" style="left:730px"><h4>HELP SPREAD THE WORD!</h4>
    <p style="font-size:12px;margin-top:-14px">Please help us spread the news about our awesome products.</p>
    <div class="share"><span>Chirp</span><span>Share</span><span>Pin it</span><span>Add</span><span>Fave</span></div>
  </div>
  <p class="copy">© 2017. All rights reserved. | www.companyname.com</p>
  <div class="pay"><span>Paylo</span><span>Payvance</span><span>Cardex</span><span>Monocard</span></div>
</footer>

</body>
</html>
```